Harborview Estates Business Card for Apartment Buildings

Create business cards for resident managers who run apartment buildings. The audience is the public who are searching for apartment rentals, and current residents who live at the apartment building. Key design element will be incorporating the company logo, however, the logo cannot dominate. The building name and manager name are more important than the logo. Current business card design leaves little room for copy, so we may need to reduce the size on the current card to allow for more space for copy.

Target Market(s)

Adults 18-65 years of age, who are looking for an apartment rental, plus current residents who live at our apartment buildings.

Industry/Entity Type

Property Management

Contact Information for Business Card

A major design element will be use of the company logo. Important property and manager contact information must be part of the design. The size of the logo will need to be reduced to make room for building and manager contact copy.

Font styles to use
Sans Serif

Colors
3176b5
000000
959595
ffffff

Requirements
Must have
• 1) Incorporate the company logo.
• 2) Use the company colors (dark blue, black/grey, over white).
• 3) FEATURE THE BUILDING NAME
• 4) FEATURE THE MANAGER NAME
• 5) The company name is less important than BUILDING and MANAGER
• 6) Manager contact information
• **SEE ATTACHED CREATIVE BRIEF**
Nice to have
• 1) Back of card logo watermark
• 2) Ability to write notes on back of carfd
Should not have
• Avoid letting the company logo dominate the card, the building name and manager are more important than the company logo.

```html
<!DOCTYPE html>
<html lang="en">
<head>
<meta charset="utf-8">
<title>Harborview Estates – Business Card</title>
<link rel="stylesheet" href="https://fonts.googleapis.com/css2?family=Arimo:wght@400;700&display=swap">
<style>
  :root {
    --brand-blue: #3176b5;
    --brand-black: #1e1f22;
    --brand-grey: #959595;
    --paper: #ffffff;
    --backdrop: #e6e7e9;
  }
  * { box-sizing: border-box; margin: 0; padding: 0; }
  html, body {
    width: 1200px; height: 780px; overflow: hidden;
    background: var(--backdrop);
    font-family: "Arimo", Arial, sans-serif;
  }
  .sheet {
    width: 1200px; height: 780px;
    display: flex; align-items: center; justify-content: center; gap: 40px;
  }
  .card {
    position: relative;
    width: 540px; height: 309px;
    background: var(--paper);
    overflow: hidden;
    box-shadow: 0 6px 18px rgba(0,0,0,.18);
  }
  .card-art { position: absolute; inset: 0; width: 100%; height: 100%; }

  .brand {
    position: absolute; left: 34px; top: 118px;
    display: flex; align-items: center; gap: 12px;
  }
  .brand-square {
    width: 26px; height: 26px; background: var(--brand-blue); flex: none;
  }
  .brand-name {
    color: var(--brand-blue); font-weight: 700;
    font-size: 25px; line-height: 1.05; letter-spacing: .5px; text-transform: uppercase;
    white-space: nowrap;
  }

  .contact {
    position: absolute; right: 18px; top: 24px;
    text-align: right; color: var(--paper);
    font-size: 11px; line-height: 1.45;
    white-space: nowrap;
  }
  .manager-name { font-size: 17px; font-weight: 700; text-transform: uppercase; letter-spacing: .3px; }
  .manager-title { font-size: 12px; margin-bottom: 16px; }
  .address { margin-bottom: 28px; }
  .web-line { font-size: 9.5px; }
</style>
</head>
<body>
<main class="sheet">

  <section class="card card-front" aria-label="Card front">
    <svg class="card-art" viewBox="0 0 540 309" preserveAspectRatio="none" aria-hidden="true">
      <path d="M296 0 Q276 200 200 309 H540 V0Z" fill="var(--brand-black)"/>
      <path d="M306 0 Q292 190 232 309 H540 V0Z" fill="var(--paper)"/>
      <path d="M310 0 Q297 190 238 309 H540 V0Z" fill="var(--brand-blue)"/>
    </svg>

    <div class="brand">
      <span class="brand-square"></span>
      <span class="brand-name">Harborview<br>Estates</span>
    </div>

    <div class="contact">
      <p class="manager-name">Daniel Whitford</p>
      <p class="manager-title">Property Manager</p>
      <p class="address">2750 Bayline Avenue #B210<br>Harbor City, CA 90710</p>
      <p class="phone-line">Phone 555-214-7730 | Fax 555-214-7731</p>
      <p class="web-line">daniel@harborviewest.com | www.harborviewest.com</p>
    </div>
  </section>

  <section class="card card-back" aria-label="Card back, space for notes">
    <svg class="card-art" viewBox="0 0 540 309" preserveAspectRatio="none" aria-hidden="true">
      <path d="M0 0 H32 Q52 180 118 309 H0Z" fill="var(--brand-black)"/>
      <path d="M0 0 H25 Q44 180 102 309 H0Z" fill="var(--paper)"/>
      <path d="M0 0 H21 Q39 180 94 309 H0Z" fill="var(--brand-blue)"/>
    </svg>
  </section>

</main>
</body>
</html>
```